Copper Ridge Inquiries Letterhead

I would like to design a letterhead for a private investigation company. Our primary clients will be law firms. The business card is included below

```html
<!DOCTYPE html>
<html lang="en">
<head>
<meta charset="utf-8">
<title>Copper Ridge Inquiries Letterhead</title>
<link rel="stylesheet" href="https://fonts.googleapis.com/css2?family=Lato:wght@400;700&family=Montserrat:wght@600;800&display=swap">
<style>
  :root {
    --navy: #1b3563;
    --orange: #ef5a2c;
    --green: #3f8f3c;
    --ink: #1d1d1f;
    --paper: #ffffff;
    --backdrop: #e7e8ea;
  }
  * { margin: 0; padding: 0; box-sizing: border-box; }
  html, body {
    width: 1200px; height: 960px; overflow: hidden;
    background: var(--backdrop);
  }
  .letterhead {
    position: absolute; left: 275px; top: 20px;
    width: 650px; height: 920px;
    background: var(--paper);
    box-shadow: 0 6px 24px rgba(0,0,0,.12);
    overflow: hidden;
    font-family: "Lato", Arial, sans-serif;
    color: var(--ink);
  }
  .header-shape, .footer-shape { position: absolute; left: 0; width: 650px; }
  .header-shape { top: 0; height: 170px; }
  .footer-shape { bottom: 0; height: 80px; }

  .contact-list {
    position: absolute; left: 355px; top: 30px;
    list-style: none;
    font-family: "Montserrat", Arial, sans-serif;
    font-weight: 600; font-size: 8.5px; letter-spacing: .6px;
    color: var(--paper); line-height: 13px;
  }
  .contact-list li { display: flex; align-items: center; gap: 6px; }
  .contact-list svg { width: 8px; height: 8px; fill: var(--orange); flex: none; }
  .contact-list .no-icon { padding-left: 14px; }

  .brand {
    position: absolute; left: 48px; top: 150px;
    display: flex; align-items: center; gap: 10px;
  }
  .brand-dot { width: 26px; height: 26px; border-radius: 50%; background: var(--orange); }
  .brand-name {
    font-family: "Lato", Arial, sans-serif; font-weight: 700;
    font-size: 19px; color: var(--navy); letter-spacing: .3px;
  }

  .letter-body {
    position: absolute; left: 62px; top: 232px; width: 540px;
    font-size: 12px; line-height: 15px;
  }
  .letter-date { margin-bottom: 16px; font-size: 13px; }
  .recipient { margin-bottom: 12px; font-size: 13px; line-height: 16px; }
  .salutation {
    font-weight: 700; color: var(--green); font-size: 16px;
    margin: 4px 0 14px;
  }
  .letter-body p.paragraph { margin-bottom: 14px; }
  .closing { margin-top: 24px; font-size: 13px; }
</style>
</head>
<body>
  <main class="letterhead">
    <svg class="header-shape" viewBox="0 0 650 170" preserveAspectRatio="none" aria-hidden="true">
      <path fill="var(--orange)" d="M0 92 C90 118 210 112 320 100 C430 90 560 120 650 112 V150 C540 132 430 120 330 118 C200 118 80 140 0 124 Z"/>
      <path fill="var(--paper)" d="M0 112 C90 132 210 122 330 110 C440 100 560 126 650 122 V170 H0 Z"/>
      <path fill="var(--navy)" d="M0 0 H650 V118 C560 124 440 98 330 104 C210 110 90 120 0 96 Z"/>
    </svg>

    <ul class="contact-list">
      <li><svg viewBox="0 0 10 10"><path d="M5 0a3.5 3.5 0 0 0-3.5 3.5C1.5 6 5 10 5 10s3.5-4 3.5-6.5A3.5 3.5 0 0 0 5 0zm0 5a1.5 1.5 0 1 1 0-3 1.5 1.5 0 0 1 0 3z"/></svg>ALDER BEND, TX</li>
      <li><svg viewBox="0 0 10 10"><path d="M2 0l2 2.5-1.2 1.2c.7 1.4 1.8 2.5 3.2 3.2L7.2 5.7 10 7.6 9 9.6C4.5 9.6.4 5.5.4 1L2 0z"/></svg>555.014.2290</li>
      <li><svg viewBox="0 0 10 10"><path d="M0 2h10v6H0zM.6 2.6 5 5.6l4.4-3H.6z"/></svg>ELLIS@COPPERRIDGEINQUIRIES.COM</li>
      <li class="no-icon">LICENSE NO. 04721936</li>
    </ul>

    <div class="brand">
      <span class="brand-dot"></span>
      <span class="brand-name">COPPER RIDGE INQUIRIES</span>
    </div>

    <section class="letter-body">
      <p class="letter-date">January-03-2020</p>
      <p class="recipient">Mr, John Doe<br>President</p>
      <p class="recipient">Link Corpppration<br>123 Street Name, Suite# 10<br>City, State, 120023</p>
      <p class="salutation">Dear Mr, John</p>
      <p class="paragraph">Lorem ipsum dolor sit amet, consectetur adipiscing elit, sed do eiusmod tempor incididunt ut labore et dolore magna aliqua. Ut enim ad minim veniam, quis nostrud exercitation ullamco laboris nisi ut aliquip ex ea commodo consequat. Duis aute irure dolor in reprehenderit in voluptate velit esse cillum dolore eu fugiat nulla pariatur.</p>
      <p class="paragraph">Lorem ipsum dolor sit amet, consectetur adipiscing elit, sed do eiusmod tempor incididunt ut labore et dolore magna aliqua. Ut enim ad minim veniam, quis nostrud exercitation ullamco laboris nisi ut aliquip ex ea commodo consequat. Duis aute irure dolor in reprehenderit in voluptate velit esse cillum dolore eu fugiat nulla pariatur.</p>
      <p class="paragraph">Lorem ipsum dolor sit amet, consectetur adipiscing elit, sed do eiusmod tempor incididunt ut labore et dolore magna aliqua. Ut enim ad minim veniam, quis nostrud exercitation ullamco laboris nisi ut aliquip ex ea commodo consequat.</p>
      <p class="paragraph">Excepteur sint occaecat cupidatat non proident, sunt in culpa qui officia deserunt mollit anim id est laborum. re et dolore magnam aliquam quaerat voluptatem.</p>
      <p class="closing">Regards</p>
    </section>

    <svg class="footer-shape" viewBox="0 0 650 80" preserveAspectRatio="none" aria-hidden="true">
      <polygon fill="var(--navy)" points="0,62 382,18 364,80 0,80"/>
      <polygon fill="var(--orange)" points="392,32 650,32 650,80 374,80"/>
    </svg>
  </main>
</body>
</html>
```